Business Card For Halvenmoor Financial Consulting

Hi, I would like a business card designed. Bold, modern.
Please use the same design as the logo. I have also attached the website design to see the overall theme.
Wordmark Font
Color: Hex: #01AEF7

```html
<!DOCTYPE html>
<html lang="en">
<head>
<meta charset="utf-8">
<title>Halvenmoor Financial Consulting — Business Card</title>
<link rel="stylesheet" href="https://fonts.googleapis.com/css2?family=Montserrat:wght@400;500;700;800&display=swap">
<style>
  :root {
    --backdrop: #3b3b3b;
    --card-navy: #16212c;
    --card-navy-deep: #111a23;
    --accent-blue: #01aef7;
    --text-white: #f2f5f7;
    --divider: #2f6f95;
  }
  * { box-sizing: border-box; margin: 0; padding: 0; }
  html, body {
    width: 1200px; height: 801px; overflow: hidden;
    background: var(--backdrop);
    font-family: "Montserrat", Arial, sans-serif;
  }
  .sheet {
    width: 1200px; height: 801px;
    display: flex; align-items: center; justify-content: center; gap: 40px;
  }
  .card {
    position: relative;
    width: 540px; height: 309px;
    background: var(--card-navy);
    border-bottom: 3px solid var(--accent-blue);
    border-left: 2px solid var(--accent-blue);
    box-shadow: 0 18px 40px rgba(0,0,0,.35);
    overflow: hidden;
  }
  /* Front */
  .brand {
    position: absolute; left: 64px; top: 58px;
    display: flex; align-items: center; gap: 16px;
  }
  .brand-square {
    width: 44px; height: 44px;
    border: 4px solid var(--accent-blue);
  }
  .brand-name {
    color: var(--text-white);
    font-weight: 700; font-size: 25px; line-height: 1.15;
    letter-spacing: 1px; text-transform: uppercase;
  }
  .details {
    position: absolute; left: 64px; top: 165px;
    display: flex; align-items: center; gap: 22px;
  }
  .person-name {
    color: var(--accent-blue);
    font-weight: 800; font-size: 19px; text-transform: uppercase; letter-spacing: .5px;
  }
  .person-title { color: var(--text-white); font-size: 14px; margin-top: 2px; text-align: right; }
  .divider { width: 1px; height: 60px; background: var(--divider); }
  .contact-list { list-style: none; color: var(--text-white); font-size: 13px; }
  .contact-list li { display: flex; align-items: center; gap: 8px; line-height: 21px; }
  .contact-list svg { width: 11px; height: 11px; flex: none; }
  .address {
    position: absolute; left: 64px; bottom: 34px;
    color: var(--text-white); font-size: 14px; letter-spacing: .2px;
  }
  /* Back */
  .pattern {
    position: absolute; inset: 0;
    background: linear-gradient(135deg, #2a3a4a 0%, var(--card-navy) 45%, var(--card-navy-deep) 100%);
  }
  .back-center {
    position: absolute; inset: 0;
    display: flex; align-items: center; justify-content: center;
  }
  .back-square {
    width: 72px; height: 72px;
    border: 5px solid var(--accent-blue);
  }
</style>
</head>
<body>
<main class="sheet">
  <section class="card card-front">
    <div class="brand">
      <div class="brand-square"></div>
      <div class="brand-name">Halvenmoor<br>Financial Consulting</div>
    </div>
    <div class="details">
      <div class="person">
        <div class="person-name">Marlo Venrick</div>
        <div class="person-title">President</div>
      </div>
      <div class="divider"></div>
      <ul class="contact-list">
        <li><svg viewBox="0 0 12 12"><path fill="#01aef7" d="M2.5 1l2 2.2-1 1.2a7 7 0 0 0 4.1 4.1l1.2-1 2.2 2-1.3 1.5C5.5 11 1 6.5 1 2.3z"/></svg>555-318-2047</li>
        <li><svg viewBox="0 0 12 12"><rect x="1" y="2.5" width="10" height="7" fill="#01aef7"/><path d="M1 2.5l5 4 5-4" stroke="#16212c" fill="none"/></svg>marlo@halvenmoor.com</li>
        <li><svg viewBox="0 0 12 12"><circle cx="6" cy="6" r="5" fill="none" stroke="#01aef7" stroke-width="1.4"/><path d="M1 6h10M6 1c-2.5 3-2.5 7 0 10M6 1c2.5 3 2.5 7 0 10" stroke="#01aef7" fill="none" stroke-width="1"/></svg>www.halvenmoor.com</li>
      </ul>
    </div>
    <p class="address">1187 Larkspur Quay, Brenton Bay CA 90412</p>
  </section>

  <section class="card card-back">
    <div class="pattern" role="img" aria-label="Repeating embossed brand-mark pattern in dark navy tones"></div>
    <div class="back-center"><div class="back-square"></div></div>
  </section>
</main>
</body>
</html>
```